ORV Web Design Project

I'm looking for a small, friendly,functional, information based website. If you go through the attachments, you would know the nature of the business.
Updates

Hi,

I have uploaded a picture of the CEO, Mr. Delvan Kroth PLMAT member. Please feel free to use it whereever appropriate.

Thanks!

Hello, I have uploaded some references. I like the colours used on the bar and would w

Example of a we page . I like this layout for the inside pages.

I am changing the tabs on my website to:

Home
About us
Services
Contact us

The services tab will have three sub pages:

Immigration
Education
AccommodationAccommodation

Target Market(s)

Young international students willing to come to Canada to study, young international students willing to immigrate to Canada, parents of the students

Industry/Entity Type

Business

Requirements
Must have
• ORV HOME
ABOUT US
CONTACT
SERVICES
TAG LINE

The website should look n feel trendy, smart, current, factual, trustworthy etc....
Nice to have
• I am looking for a bold, attractive, eye catchy home page with less text! Something that makes a statement....
Should not have
• No Clip art, flash animation, no bells n whistles please

```html
<!DOCTYPE html>
<html lang="en">
<head>
<meta charset="utf-8">
<title>ORV – Contact</title>
<link rel="stylesheet" href="https://fonts.googleapis.com/css2?family=Open+Sans:wght@400;600;700&family=Righteous&display=swap">
<style>
  :root {
    --brand-red: #d9121b;
    --bg-red-dark: #6f0009;
    --bg-red: #a50413;
    --ink: #1c1c1c;
    --nav-grey: #7a7a7a;
    --accent-orange: #f39322;
    --band-grey: #f1f1f1;
    --field-border: #d6d6d6;
    --slate: #44505a;
    --white: #ffffff;
    --map-tone: #ece9e2;
  }
  * { box-sizing: border-box; margin: 0; padding: 0; }
  html, body { width: 1200px; height: 974px; overflow: hidden; }
  body {
    position: relative;
    background: linear-gradient(180deg, var(--bg-red-dark) 0%, var(--bg-red) 35%, var(--bg-red) 100%);
    font-family: "Open Sans", Arial, sans-serif;
    color: var(--ink);
  }
  .page {
    position: absolute; left: 96px; top: 49px; width: 1008px; height: 850px;
    background: var(--white); border-radius: 4px; overflow: hidden;
  }
  .brand {
    position: absolute; left: 34px; top: 76px;
    display: flex; align-items: center; gap: 12px;
  }
  .brand-name { font-weight: 700; font-size: 64px; line-height: 1; color: var(--ink); letter-spacing: 1px; }
  .brand-mark { width: 26px; height: 26px; background: var(--brand-red); }
  .tagline {
    position: absolute; right: 36px; top: 68px;
    font-family: "Righteous", "Arial Black", sans-serif; font-size: 38px; letter-spacing: 1px; color: var(--ink);
  }
  .tagline em { font-style: normal; color: var(--brand-red); }
  .main-nav { position: absolute; right: 36px; top: 122px; display: flex; gap: 26px; }
  .main-nav a { font-size: 17px; color: var(--nav-grey); text-decoration: none; }
  .main-nav a.is-active { color: var(--accent-orange); }

  .contact-band { position: absolute; left: 0; top: 203px; width: 1008px; height: 447px; background: var(--band-grey); }
  .map {
    position: absolute; left: 34px; top: 29px; width: 528px; height: 307px;
    background: linear-gradient(135deg, #e9e6dc, var(--map-tone) 60%, #dfe8d6);
    border: 5px solid var(--white); box-shadow: 0 1px 4px rgba(0,0,0,.25);
  }
  .details { position: absolute; top: 369px; display: flex; font-size: 12px; line-height: 16px; }
  .detail { position: absolute; top: 0; white-space: nowrap; }
  .detail h3 { font-size: 12px; font-weight: 700; letter-spacing: .3px; }
  .detail a { color: var(--brand-red); text-decoration: none; }

  .contact-form { position: absolute; left: 601px; top: 27px; width: 364px; }
  .contact-form label { display: block; font-size: 12px; font-weight: 700; letter-spacing: .5px; margin-bottom: 5px; }
  .field {
    display: block; width: 364px; height: 30px; background: var(--white);
    border: 1px solid var(--field-border); margin-bottom: 15px;
  }
  .field.message { height: 148px; margin-bottom: 12px; }
  .submit {
    display: block; width: 178px; height: 40px;
    background: linear-gradient(180deg, #f7a23a, var(--accent-orange));
    border: 1px solid #c9731a; box-shadow: 0 1px 2px rgba(0,0,0,.3);
    color: var(--white); font-family: inherit; font-size: 14px; font-weight: 600; letter-spacing: .5px;
  }

  .closing { position: absolute; left: 199px; top: 700px; display: flex; align-items: center; gap: 26px; }
  .closing-brand { display: flex; align-items: center; gap: 8px; }
  .closing-brand .brand-name { font-size: 40px; }
  .closing-brand .brand-mark { width: 16px; height: 16px; }
  .motto { font-size: 31px; color: var(--slate); letter-spacing: .5px; line-height: 1; }
  .motto em { font-style: normal; color: var(--brand-red); }
  .motto-sub { font-size: 14px; color: var(--slate); margin-top: 6px; }

  .copyright { position: absolute; left: 0; top: 926px; width: 1200px; text-align: center; font-size: 11px; color: var(--white); }
</style>
</head>
<body>
  <div class="page">
    <header>
      <div class="brand"><span class="brand-name">ORV</span><span class="brand-mark"></span></div>
      <div class="tagline">Taking You <em>Onwards</em></div>
      <nav class="main-nav">
        <a href="#">Home</a>
        <a href="#">About Us</a>
        <a href="#">Services</a>
        <a href="#" class="is-active">Contact</a>
        <a href="#">ORV Mission</a>
      </nav>
    </header>

    <section class="contact-band">
      <div class="map" role="img" aria-label="Street map showing the office location"></div>
      <div class="details">
        <div class="detail" style="left:38px"><h3>ADDRESS :</h3>48 Alder Row, Kelwood,<br>Ontario, K2P 3R8 Canada</div>
        <div class="detail" style="left:233px"><h3>PHONE :</h3>(555) 210 4471<br>(555) 210 4472</div>
        <div class="detail" style="left:368px"><h3>EMAIL :</h3><a href="#">hello@orvanebridge.com</a></div>
      </div>
      <form class="contact-form">
        <label>NAME</label><span class="field"></span>
        <label>EMAIL</label><span class="field"></span>
        <label>MESSAGE</label><span class="field message"></span>
        <button type="button" class="submit">SUBMIT</button>
      </form>
    </section>

    <section class="closing">
      <div class="closing-brand"><span class="brand-name">ORV</span><span class="brand-mark"></span></div>
      <div>
        <div class="motto">DARE TO DREAM <em>CANADIAN</em></div>
        <div class="motto-sub">Your best partner for immigration &amp; education solution in Canada.</div>
      </div>
    </section>
  </div>
  <footer class="copyright">Copyright © 2013 OrvaneBridgeGroup. All Rights Reserved.</footer>
</body>
</html>
```